SOLVE Study flyer

I need help designing a flyer for a research study that will include brain imaging in adolescents. The info is in the attached document. The study is called the Sequoia Outlook Lantern Valley Echo (SOLVE) study. Ideally this would be returned as a document that I can edit in the future as we will have several new recruitment phases (different age groups, etc. I also would love to have a logo designed as part of this project, but I recognize that might be a separate design request.

```html
<!DOCTYPE html>
<html lang="en">
<head>
<meta charset="utf-8">
<title>SOLVE Study Recruitment Flyer</title>
<link href="https://fonts.googleapis.com/css2?family=League+Gothic&family=Bebas+Neue&family=Poppins:wght@500;600;700;800&family=Lato:wght@400;700&display=swap" rel="stylesheet">
<style>
  :root {
    --backdrop: #a7a8ab;
    --paper: #ffffff;
    --hero-bg: #f3f3f3;
    --navy: #0c1833;
    --teal: #13a39a;
    --purple: #5b3a9b;
    --orange: #f47b20;
    --sky: #1aa8e8;
    --gold: #f5c211;
    --ink: #222222;
    --lavender: #ece8f4;
    --mint: #e5f3f2;
    --grey-disc: #e6e6e8;
  }
  * { box-sizing: border-box; margin: 0; padding: 0; }
  html, body { width: 950px; height: 1200px; overflow: hidden; }
  body { background: var(--backdrop); position: relative; font-family: "Lato", sans-serif; color: var(--ink); }

  .flyer { position: absolute; left: 104px; top: 120px; width: 742px; height: 960px; background: var(--paper); overflow: hidden; }

  .hero { position: absolute; left: 0; top: 0; width: 742px; height: 385px; background: linear-gradient(90deg, #ffffff 0%, var(--hero-bg) 60%); }
  .hero-photo { position: absolute; left: 334px; top: 0; width: 408px; height: 385px;
    background: radial-gradient(circle at 78% 45%, #f7d35a 0%, #f08aa8 28%, #b9a6dc 48%, rgba(230,230,230,0) 70%), linear-gradient(90deg, #f3f3f3 0%, #e9e9e9 100%); }

  .brand { position: absolute; left: 71px; top: 52px; display: flex; align-items: center; gap: 8px; }
  .brand-mark { width: 20px; height: 20px; background: var(--navy); }
  .brand-name { font-family: "Poppins", sans-serif; font-weight: 600; font-size: 15px; color: var(--navy); }

  .headline { position: absolute; left: 71px; top: 115px; font-family: "League Gothic", "Bebas Neue", sans-serif; color: #fff; font-weight: 400; }
  .headline span { display: block; font-size: 68px; line-height: 1; padding: 3px 0 0 12px; white-space: nowrap; overflow: hidden; }
  .headline .line-1 { background: var(--navy); width: 275px; height: 69px; }
  .headline .line-2 { background: var(--teal); width: 270px; height: 67px; }
  .headline .line-3 { background: var(--purple); width: 328px; height: 59px; padding-top: 0; }

  .subhead { position: absolute; left: 93px; top: 319px; font-family: "Bebas Neue", sans-serif; font-size: 28px; line-height: 33px; color: var(--ink); white-space: nowrap; }
  .subhead em { font-style: normal; color: var(--orange); }

  .intro-icon { position: absolute; left: 104px; top: 405px; width: 114px; height: 114px; }
  .intro-rule { position: absolute; left: 236px; top: 411px; width: 1px; height: 100px; background: #cfcfcf; }
  .intro-text { position: absolute; left: 255px; top: 417px; width: 405px; font-family: "Poppins", sans-serif; font-weight: 600; font-size: 14.3px; line-height: 21px; color: var(--ink); }

  .panel { position: absolute; top: 536px; height: 271px; border-radius: 8px; }
  .panel-participation { left: 62px; width: 330px; background: var(--lavender); }
  .panel-eligibility { left: 406px; width: 278px; background: var(--mint); }
  .panel-title { position: absolute; font-family: "Poppins", sans-serif; font-weight: 700; font-size: 19.5px; line-height: 26px; letter-spacing: -0.3px; }
  .panel-participation .panel-title { left: 13px; top: 14px; color: var(--purple); }
  .panel-eligibility .panel-title { left: 23px; top: 19px; color: var(--navy); }
  .panel-title .accent { color: var(--teal); }

  .task { position: absolute; left: 78px; width: 245px; font-size: 14px; line-height: 17.6px; color: #333; }
  .task strong { font-weight: 700; color: var(--ink); }
  .task-icon { position: absolute; left: 19px; width: 39px; height: 39px; border-radius: 50%; display: flex; align-items: center; justify-content: center; }

  .criterion { position: absolute; left: 63px; width: 205px; font-size: 16.5px; line-height: 20px; color: var(--ink); }
  .check { position: absolute; left: 24px; width: 22px; height: 22px; }
  .criterion-rule { position: absolute; left: 63px; width: 187px; height: 1px; background: var(--teal); opacity: 0.7; }

  .footer { position: absolute; left: 0; top: 821px; width: 742px; height: 139px; background: var(--navy); color: #fff; }
  .footer-disc { position: absolute; width: 84px; height: 84px; border-radius: 50%; display: flex; align-items: center; justify-content: center; }
  .contact-disc { left: 48px; top: 27px; background: var(--teal); }
  .reward-disc { left: 403px; top: 33px; background: var(--gold); }
  .contact-title { position: absolute; left: 147px; top: 17px; font-family: "Poppins", sans-serif; font-weight: 700; font-size: 17px; line-height: 22px; }
  .contact-note { position: absolute; left: 145px; top: 63px; font-family: "Poppins", sans-serif; font-weight: 500; font-size: 11.5px; line-height: 14px; }
  .contact-email { position: absolute; left: 145px; top: 96px; font-family: "Poppins", sans-serif; font-weight: 500; font-size: 15px; white-space: nowrap; }
  .footer-rule { position: absolute; left: 375px; top: 20px; width: 1px; height: 100px; background: #6c7488; }
  .reward-title { position: absolute; left: 501px; top: 33px; font-family: "Poppins", sans-serif; font-weight: 700; font-size: 20.5px; }
  .reward-upto { position: absolute; left: 503px; top: 63px; font-family: "Poppins", sans-serif; font-weight: 700; font-size: 18px; line-height: 22px; }
  .reward-amount { position: absolute; left: 539px; top: 52px; font-family: "Poppins", sans-serif; font-weight: 800; font-size: 58px; line-height: 70px; color: var(--gold); letter-spacing: -1px; }
</style>
</head>
<body>
<main class="flyer">

  <section class="hero">
    <div class="hero-photo" role="img" aria-label="Photo of a thoughtful teenage girl in front of a brain illustration, half line drawing with math formulas, half colourful paint splashes"></div>

    <div class="brand">
      <span class="brand-mark"></span>
      <span class="brand-name">Northvale University</span>
    </div>

    <h1 class="headline">
      <span class="line-1">ARE YOU THE</span>
      <span class="line-2">PARENT OF A</span>
      <span class="line-3">CHILD AGE 10-17?</span>
    </h1>

    <p class="subhead">Do they <em>worry or overthink</em><br>negative emotions?</p>
  </section>

  <section class="intro">
    <svg class="intro-icon" viewBox="0 0 114 114" aria-hidden="true">
      <circle cx="57" cy="57" r="57" fill="var(--grey-disc)"/>
      <g stroke="var(--gold)" stroke-width="2" stroke-linecap="round">
        <line x1="57" y1="10" x2="57" y2="19"/><line x1="57" y1="95" x2="57" y2="104"/>
        <line x1="10" y1="57" x2="19" y2="57"/><line x1="95" y1="57" x2="104" y2="57"/>
        <line x1="34" y1="18" x2="38" y2="25"/><line x1="80" y1="18" x2="76" y2="25"/>
        <line x1="34" y1="96" x2="38" y2="89"/><line x1="80" y1="96" x2="76" y2="89"/>
        <line x1="17" y1="36" x2="24" y2="40"/><line x1="97" y1="36" x2="90" y2="40"/>
        <line x1="17" y1="78" x2="24" y2="74"/><line x1="97" y1="78" x2="90" y2="74"/>
      </g>
      <g fill="none" stroke="var(--ink)" stroke-width="2.2">
        <ellipse cx="47" cy="57" rx="13" ry="19"/>
        <ellipse cx="67" cy="57" rx="13" ry="19"/>
        <line x1="57" y1="40" x2="57" y2="74"/>
      </g>
    </svg>
    <div class="intro-rule"></div>
    <p class="intro-text">Northvale University researchers are seeking girls age 10-17 for a study about brain activity in emotions and decision-making and how they relate to puberty, anxiety and depression.</p>
  </section>

  <section class="panel panel-participation">
    <h2 class="panel-title">STUDY PARTICIPATION<br>INVOLVES:</h2>

    <div class="task-icon" style="top:83px;background:var(--teal)">
      <svg width="20" height="20" viewBox="0 0 20 20" fill="none" stroke="#fff" stroke-width="1.3"><rect x="3" y="5" width="14" height="10"/><circle cx="10" cy="9" r="2"/><path d="M7 14c0-2 6-2 6 0M1 17h18"/></svg>
    </div>
    <p class="task" style="top:77px"><strong>One one-hour interview</strong><br>(online or in-person) where your child will discuss their thoughts</p>

    <div class="task-icon" style="top:141px;background:var(--purple)">
      <svg width="18" height="20" viewBox="0 0 18 20" fill="none" stroke="#fff" stroke-width="1.3"><rect x="3" y="2" width="12" height="16"/><path d="M5 6h2M9 6h4M5 10h2M9 10h4M5 14h2M9 14h4"/></svg>
    </div>
    <p class="task" style="top:139px"><strong>Online questionnaires</strong><br>(parent and child)</p>

    <div class="task-icon" style="top:207px;background:var(--sky)">
      <svg width="22" height="22" viewBox="0 0 22 22" fill="none" stroke="#fff" stroke-width="1.4"><circle cx="11" cy="11" r="9"/><path d="M11 5v6l4 3"/></svg>
    </div>
    <p class="task" style="top:184px"><strong>One two-hour visit</strong> where your child will complete an MRI scan, answer questions about their puberty stage, and have a small hair sample taken to study puberty hormones</p>
  </section>

  <section class="panel panel-eligibility">
    <h2 class="panel-title"><span class="accent">YOUR CHILD MAY</span><br>BE ELIGIBLE IF THEY:</h2>

    <svg class="check" style="top:81px" viewBox="0 0 22 22"><circle cx="11" cy="11" r="11" fill="var(--teal)"/><path d="M6 11l3.5 3.5L16 8" fill="none" stroke="#fff" stroke-width="1.8"/></svg>
    <p class="criterion" style="top:82px">Are age 10-17</p>
    <div class="criterion-rule" style="top:116px"></div>

    <svg class="check" style="top:132px" viewBox="0 0 22 22"><circle cx="11" cy="11" r="11" fill="var(--teal)"/><path d="M6 11l3.5 3.5L16 8" fill="none" stroke="#fff" stroke-width="1.8"/></svg>
    <p class="criterion" style="top:130px">Tend to worry or overthink negative thoughts</p>
    <div class="criterion-rule" style="top:186px"></div>

    <svg class="check" style="top:199px" viewBox="0 0 22 22"><circle cx="11" cy="11" r="11" fill="var(--teal)"/><path d="M6 11l3.5 3.5L16 8" fill="none" stroke="#fff" stroke-width="1.8"/></svg>
    <p class="criterion" style="top:198px">Have not been diagnosed with psychosis, learning problems, or autism</p>
  </section>

  <footer class="footer">
    <div class="footer-disc contact-disc">
      <svg width="48" height="36" viewBox="0 0 48 36" fill="none" stroke="var(--navy)" stroke-width="3.5" stroke-linejoin="round"><rect x="2" y="2" width="44" height="32" rx="2"/><path d="M2 3l22 17L46 3M2 34l16-14M46 34L30 20"/></svg>
    </div>
    <p class="contact-title">INTERESTED IN<br>PARTICIPATING?</p>
    <p class="contact-note">Want more information?<br>Please contact us!</p>
    <p class="contact-email">solvestudy@northvale.edu</p>

    <div class="footer-rule"></div>

    <div class="footer-disc reward-disc">
      <svg width="44" height="46" viewBox="0 0 44 46" fill="none" stroke="var(--navy)" stroke-width="3" stroke-linejoin="round"><rect x="4" y="15" width="36" height="9"/><rect x="7" y="24" width="30" height="20"/><path d="M18 15v29M26 15v29M22 15c-4-10-14-9-10-2 2 2 6 2 10 2zM22 15c4-10 14-9 10-2-2 2-6 2-10 2z"/></svg>
    </div>
    <p class="reward-title">COMPENSATION</p>
    <p class="reward-upto">UP<br>TO</p>
    <p class="reward-amount">$140</p>
  </footer>

</main>
</body>
</html>
```